Business Card Design for Varomir Facility Services

We are looking for a Business Card Design for the Company "Varomir Facility Services."
Front side:
- Company Logo (small)
- Company Name, address, pohone, website and personal data.
- white background, for text e.g. company colors (blue or green like in the logo)
Please use following data:
Company data:
Varomir Facility Services Kostelac
Birkenhaldweg 14
6318 Brunnmatt
www.varomir-fs.ch
Person data:
Tarik Kostelac
Geschäftsführer
+41 76 519 47 83
info@varomir-fs.ch
Back side:
could be colored in blue or green
please use a big logo sing and some smaller icons to say what is all beeing offered in facility services, like cleaning, maintenance cleaning
industrial cleaning, caretaking, gardening, disposal. There is no need for everyone of the icons if there are similar or an icon is standing for more of them.
colors to use:
blue: HEX 246BB0
green: HEX 52B33E

```html
<!DOCTYPE html>
<html lang="de">
<head>
<meta charset="utf-8">
<title>Varomir Facility Services – Business Card</title>
<link href="https://fonts.googleapis.com/css2?family=Arimo:wght@400;700&display=swap" rel="stylesheet">
<style>
  :root {
    --blue: #246BB0;
    --green: #52B33E;
    --white: #ffffff;
    --stage: #d6d6d6;
    --shadow: rgba(0,0,0,0.22);
  }
  * { margin: 0; padding: 0; box-sizing: border-box; }
  html, body { width: 1200px; height: 900px; overflow: hidden; }
  body {
    background: var(--stage);
    font-family: "Arimo", Arial, sans-serif;
    position: relative;
  }
  .card {
    position: absolute;
    width: 560px;
    height: 320px;
    overflow: hidden;
    box-shadow: 0 8px 18px var(--shadow);
  }
  .card-shape { position: absolute; inset: 0; width: 100%; height: 100%; }

  /* Back side */
  .card-back { left: 60px; top: 100px; background: var(--blue); }
  .back-brand {
    position: absolute; left: 110px; top: 188px;
    color: var(--white); font-weight: 700; font-size: 28px; line-height: 1.12;
    display: flex; align-items: center; gap: 12px;
  }
  .brand-dot { width: 16px; height: 16px; border-radius: 50%; background: var(--green); flex: none; }
  .service-list {
    position: absolute; left: 396px; top: 30px;
    list-style: none; display: flex; flex-direction: column; gap: 12px;
  }
  .service {
    display: flex; align-items: center; gap: 14px;
    color: var(--white); font-size: 14px; line-height: 1.15;
  }
  .service-icon {
    width: 30px; height: 30px; border-radius: 6px;
    background: var(--green); flex: none;
  }

  /* Front side */
  .card-front { left: 580px; top: 480px; background: var(--white); }
  .front-brand {
    position: absolute; left: 36px; top: 50px;
    color: var(--blue); font-weight: 700; font-size: 21px; line-height: 1.15;
    display: flex; align-items: center; gap: 10px;
  }
  .front-brand .brand-dot { width: 14px; height: 14px; }
  .person {
    position: absolute; left: 260px; top: 56px; width: 160px; text-align: right;
  }
  .person-name { color: var(--green); font-weight: 700; font-size: 17px; }
  .person-role { color: var(--blue); font-size: 13px; margin-top: 4px; }
  .contact {
    position: absolute; left: 36px; bottom: 34px;
    color: var(--blue); font-size: 13px; line-height: 1.45; font-style: normal;
  }
  .contact-address { margin-bottom: 4px; }
  .contact-row { display: flex; align-items: center; gap: 7px; }
  .contact-icon { width: 12px; height: 12px; flex: none; }
</style>
</head>
<body>

  <section class="card card-back" aria-label="Business card back side">
    <svg class="card-shape" viewBox="0 0 560 320" preserveAspectRatio="none" aria-hidden="true">
      <path d="M0 150 C20 250 110 308 260 320 L0 320 Z" fill="var(--green)"/>
      <path d="M24 140 C44 255 150 314 300 324" fill="none" stroke="var(--blue)" stroke-width="7"/>
      <path d="M38 128 C58 245 165 308 330 324" fill="none" stroke="var(--green)" stroke-width="5"/>
    </svg>
    <div class="back-brand"><span class="brand-dot"></span><span>Varomir<br>Facility Services</span></div>
    <ul class="service-list">
      <li class="service"><span class="service-icon" role="img" aria-label="Cleaning icon"></span>Cleaning</li>
      <li class="service"><span class="service-icon" role="img" aria-label="Maintenance cleaning icon"></span>Maintenance<br>Cleaning</li>
      <li class="service"><span class="service-icon" role="img" aria-label="Industrial cleaning icon"></span>Industrial<br>Cleaning</li>
      <li class="service"><span class="service-icon" role="img" aria-label="Gardening icon"></span>Gardening</li>
      <li class="service"><span class="service-icon" role="img" aria-label="Disposal icon"></span>Disposal</li>
    </ul>
  </section>

  <section class="card card-front" aria-label="Business card front side">
    <svg class="card-shape" viewBox="0 0 560 320" preserveAspectRatio="none" aria-hidden="true">
      <path d="M440 0 L560 0 L560 320 L500 320 C560 200 540 60 440 0 Z" fill="var(--blue)"/>
      <path d="M420 0 C530 50 545 200 484 322" fill="none" stroke="var(--white)" stroke-width="14"/>
      <path d="M408 2 C515 55 528 200 470 322" fill="none" stroke="var(--green)" stroke-width="6"/>
    </svg>
    <div class="front-brand"><span class="brand-dot"></span><span>Varomir<br>Facility Services</span></div>
    <div class="person">
      <p class="person-name">Tarik Kostelac</p>
      <p class="person-role">Geschäftsführer</p>
    </div>
    <address class="contact">
      <p class="contact-address">Birkenhaldweg 14<br>6318 Brunnmatt</p>
      <p class="contact-row">
        <svg class="contact-icon" viewBox="0 0 12 12" aria-hidden="true"><path d="M2 1 L4.5 1 L5.2 3.6 L3.8 4.6 C4.5 6 6 7.5 7.4 8.2 L8.4 6.8 L11 7.5 L11 10 C6 11 1 6 2 1 Z" fill="var(--green)"/></svg>
        +41 76 519 47 83
      </p>
      <p class="contact-row">
        <svg class="contact-icon" viewBox="0 0 12 12" aria-hidden="true"><rect x="1" y="2.5" width="10" height="7" fill="none" stroke="var(--green)" stroke-width="1.3"/><path d="M1 2.5 L6 6.5 L11 2.5" fill="none" stroke="var(--green)" stroke-width="1.3"/></svg>
        info@varomir-fs.ch
      </p>
      <p class="contact-row">
        <svg class="contact-icon" viewBox="0 0 12 12" aria-hidden="true"><circle cx="6" cy="6" r="5" fill="var(--green)"/><path d="M1 6 H11 M6 1 C3.5 4 3.5 8 6 11 M6 1 C8.5 4 8.5 8 6 11" fill="none" stroke="var(--white)" stroke-width="0.9"/></svg>
        www.varomir-fs.ch
      </p>
    </address>
  </section>

</body>
</html>
```